Corrimal Lodge Web Design Project

I am looking for a striking, modern and user friendly site to promote my business, Corrimal Lodge.

Corrimal Lodge comprises of 3 elements : Restaurant, Resort and Events and the site must showcase all of these.
Updates

Project Deadline Extended
Reason: Too far away from brief ! Please check out the 2 website links to restaurant sites i LOVE for inspiration ! I am happy to pay for a quality designer and also for anyone that can code this !

Target Market(s)

Our Restaurant clientele demographic is 30-60 years old and are a mix of locals and tourists. The Restaurant is very much a destination venue so we attract people that wish to seek out amazing food.

The Event side of things attracts mainly weddings, this is a lucrative arm of the business and this side of the site must also be outstanding.

The Resort comprises of 7 boutique loft apartment and has a big pool and spa. We attract a mix of locals but want to push it as a ' getaway '

Industry/Entity Type

Business

Requirements
Must have
• I would like the first page to be an overall blog and to highlight the 3 area of the business. Lets have the 3 keywords as clickable tabs that take you to that section of the site.

RESTAURANT RESORT EVENTS

The RESTAURANT page should include the following tabs ( i have provided the information to be added to each tab as an example )

MENU ( Breakfast, Lunch, Dinner, Set Menu, Wine List)

FUNCTIONS (Private Dining Room, Exclusive Use, Wine Nights Coming Soon)

RESERVATIONS (Enquiry Form linked to my info@ address, Reservation Policies, Contact Number)

GALLERY & PRESS ( Press Articles, Latest News, What's On, Photo's, Wedding Hot Spot)

CONTACT US (Opening Times, Map, Contact Details, Sign Up For Our Newsletter, Facebook Link )

The RESORT page should include the following tabs :
# LOFTS & RATES
# FACILITIES
# SPECIAL OFFERS
# GALLERY
# RESERVATIONS

The EVENTS page should include the following tabs :
# WEDDINGS
# CONFERENCES
# PRIVATE EVENTS
# GALLERY
# ENQUIRY FORM
Nice to have
• Include Logo, good branding

```html
<!DOCTYPE html>
<html lang="en">
<head>
<meta charset="utf-8">
<title>Corrimal Lodge — Resort</title>
<link href="https://fonts.googleapis.com/css2?family=Parisienne&family=Arimo&display=swap" rel="stylesheet">
<style>
  :root {
    --wood-light: #e2b88a;
    --wood-mid: #cf9d6c;
    --wood-dark: #b98556;
    --plank-line: rgba(110, 65, 30, 0.35);
    --brand-red: #8c1212;
    --brand-red-dark: #6a0b0b;
    --cream: rgba(250, 244, 236, 0.93);
    --ink: #2a1a12;
    --rule: #e8b98a;
    --white: #ffffff;
    --social-blue: #2b6fc4;
  }
  * { box-sizing: border-box; margin: 0; padding: 0; }
  html, body { width: 1200px; height: 1050px; overflow: hidden; }
  body {
    position: relative;
    font-family: "Arimo", Arial, sans-serif;
    background:
      repeating-linear-gradient(90deg, transparent 0 79px, var(--plank-line) 79px 81px),
      linear-gradient(90deg, var(--wood-mid), var(--wood-light) 30%, var(--wood-mid) 55%, var(--wood-light) 80%, var(--wood-dark));
  }
  .site-title {
    position: absolute; left: 387px; top: 44px; width: 450px; height: 69px;
    border-radius: 50%;
    background: radial-gradient(ellipse at 50% 40%, #a81818, var(--brand-red) 60%, var(--brand-red-dark));
    box-shadow: 0 3px 6px rgba(0,0,0,0.35);
    display: flex; align-items: center; justify-content: center;
    font-family: "Parisienne", cursive; font-size: 44px; color: var(--white);
  }
  .brand-mark {
    position: absolute; left: 940px; top: 42px; width: 110px;
    display: flex; flex-direction: column; align-items: center; gap: 6px;
    font-family: "Arimo", Arial, sans-serif; font-size: 13px; color: var(--white);
  }
  .brand-mark .square { width: 50px; height: 50px; border: 2px solid var(--white); }
  .social { position: absolute; top: 51px; display: flex; gap: 18px; left: 1050px; }
  .social a {
    display: block; width: 48px; height: 48px; border-radius: 50%;
    background: var(--white); border: 3px solid var(--social-blue);
  }
  .sr { position: absolute; width: 1px; height: 1px; overflow: hidden; clip: rect(0 0 0 0); }
  .section-tile {
    position: absolute; left: 30px; width: 144px; height: 123px;
    background: var(--brand-red); border-radius: 4px;
    box-shadow: 3px 4px 6px rgba(0,0,0,0.4);
    text-decoration: none;
  }
  .section-tile .label {
    display: block; text-align: center; font-family: "Parisienne", cursive;
    font-size: 24px; color: var(--white); line-height: 32px;
  }
  .section-tile .photo { position: absolute; left: 9px; right: 9px; top: 33px; bottom: 9px; }
  .tile-restaurant { top: 112px; }
  .tile-restaurant .photo { background: linear-gradient(180deg, #d9c7a6, #9a6b45 60%, #5a3022); }
  .tile-resort { top: 260px; }
  .tile-resort .photo { background: linear-gradient(180deg, #7fb4e4, #c9a777 45%, #2e9fc9 80%); }
  .tile-events { top: 410px; left: 27px; width: 150px; height: 127px; }
  .tile-events .photo { background: linear-gradient(180deg, #b7cde0, #4d7a3e 50%, #e9e6e2 85%); }
  .resort-nav {
    position: absolute; left: 246px; top: 250px; width: 174px; height: 565px;
    background: var(--cream);
  }
  .resort-nav ul { list-style: none; }
  .resort-nav .rule {
    position: absolute; left: 22px; right: 22px; height: 1px; background: var(--rule);
  }
  .resort-nav a {
    position: absolute; left: 0; right: 0; text-align: center;
    font-family: "Parisienne", cursive; font-size: 26px; color: var(--ink);
    text-decoration: none;
  }
  .hero-frame {
    position: absolute; left: 465px; top: 201px; width: 618px; height: 737px;
    background: var(--brand-red); box-shadow: 3px 4px 8px rgba(0,0,0,0.35);
  }
  .hero-photo {
    position: absolute; left: 27px; top: 21px; width: 569px; height: 695px;
    background: linear-gradient(180deg, #4e8fd6 0%, #d9c594 22%, #b07a45 45%, #7a5a38 62%, #5f8a46 72%, #2f9fd2 82%, #1a7fc0 100%);
  }
  .site-footer {
    position: absolute; top: 1012px; left: 0; width: 1200px; height: 24px;
    font-size: 19px; color: var(--white);
  }
  .site-footer .copyright { position: absolute; left: 261px; }
  .site-footer .privacy { position: absolute; left: 760px; color: var(--white); text-decoration: none; }
</style>
</head>
<body>
  <header>
    <h1 class="site-title">Corrimal Lodge</h1>
    <div class="brand-mark"><span class="square"></span><span>Corrimal Lodge</span></div>
    <nav class="social" aria-label="Social links">
      <a href="#" aria-label="Social page one"><span class="sr">Social page one</span></a>
      <a href="#" aria-label="Social page two"><span class="sr">Social page two</span></a>
    </nav>
  </header>

  <nav aria-label="Sections">
    <a class="section-tile tile-restaurant" href="#"><span class="label">Restaurant</span><span class="photo" role="img" aria-label="Restaurant dining room with set tables"></span></a>
    <a class="section-tile tile-resort" href="#"><span class="label">Resort</span><span class="photo" role="img" aria-label="Resort building beside the pool"></span></a>
    <a class="section-tile tile-events" href="#"><span class="label">Events</span><span class="photo" role="img" aria-label="Outdoor event tables on the lawn"></span></a>
  </nav>

  <nav class="resort-nav" aria-label="Resort">
    <span class="rule" style="top:14px"></span>
    <a href="#" style="top:48px">Loft &amp; Rates</a>
    <span class="rule" style="top:105px"></span>
    <a href="#" style="top:136px">Facilities</a>
    <span class="rule" style="top:210px"></span>
    <a href="#" style="top:244px">Special Offers</a>
    <span class="rule" style="top:317px"></span>
    <a href="#" style="top:349px">Gallery</a>
    <span class="rule" style="top:425px"></span>
    <a href="#" style="top:464px">Reservations</a>
    <span class="rule" style="top:542px"></span>
  </nav>

  <main class="hero-frame">
    <div class="hero-photo" role="img" aria-label="Three-storey loft building with balconies above a curved blue swimming pool"></div>
  </main>

  <footer class="site-footer">
    <span class="copyright">copyright Corrimal Lodge 2013</span>
    <a class="privacy" href="#">Privacy Policy</a>
  </footer>
</body>
</html>
```